A New and modern Business Card for Tarwick Trade Solutions Ltd

New and modern Logo and Business Card Attached is the current logo/business card designCurrently the business is called "Tarwick & Co." or TTS Ltd for short. This is subject to change.This business specialises in Telecoms and Energy. We work with the major networks (QV, K7, etc) and also offer Energy Products saving clients money off their energy bills.These are business to business services.The current design incorporates a Pheonix, indicating rebirth, starting something new.We would like to maintain the Phoenix element but a newer modern style.We love colours in the logo 3 max.The aim of this is to be ultra slick and modern. I envisage Tarwick & Co. on one side of the card with long descriptions on the other side.Side 1:TTS Ltd/Logo?Side 2:TTS Ltd/Logo/Graphic?Tarwick & Co.Name:Address:Phone:Email:The design is mostly flexible but must incorporate a Phoenix.For example "Tarwick & Co." with a block phoenix behind the text...up to you.

Industry/Entity Type

Telecommunications

Contact Information for Business Card

Tarwick & Co.
Address:
Name:
Phone:
Email:

Logo Text

Tarwick & Co.

Colors
33a6d7
0792cd
acd037
9bcb3c
f78f20
fece3e

Requirements
Must have
• Phoenix
• 3/4 colours max
• Blue representing Technology (wireless)
• Green for Eco Energy
• Orange for Phoenix
• White business card background
Should not have
• phoenix must not all be red/ orange fire, we are a technology service company and the phoenix colours must represent this. Fire is not representative of our company.

```html
<!DOCTYPE html>
<html lang="en">
<head>
<meta charset="utf-8">
<title>Tarwick & Co. — Business Card</title>
<link rel="stylesheet" href="https://fonts.googleapis.com/css2?family=Cinzel:wght@400;500&family=Lato:wght@400;700&display=swap">
<style>
  :root {
    --bg: #e6e6e8;
    --card-white: #ffffff;
    --ink: #2b2b2b;
    --ink-soft: #444444;
    --orange: #f78f20;
    --amber: #d9a21a;
    --green: #7cc423;
    --green-deep: #4fb548;
    --blue: #33a6d7;
    --teal: #1fa7a0;
    --name-green: #8cc63f;
    --shadow: 0 18px 30px rgba(0,0,0,0.22), 0 4px 8px rgba(0,0,0,0.12);
  }
  * { box-sizing: border-box; margin: 0; padding: 0; }
  html, body { width: 1200px; height: 900px; overflow: hidden; }
  body {
    background: radial-gradient(ellipse at 50% 40%, #f2f2f3 0%, var(--bg) 70%);
    font-family: "Lato", sans-serif;
    position: relative;
  }
  .card {
    position: absolute;
    width: 540px;
    height: 310px;
    border-radius: 26px;
    box-shadow: var(--shadow);
    overflow: hidden;
  }
  /* Front side */
  .card--front {
    left: 90px;
    top: 130px;
    background: linear-gradient(168deg, var(--amber) 0%, #a9b81a 30%, var(--green) 55%, var(--green-deep) 78%, var(--blue) 100%);
  }
  .front__glow {
    position: absolute;
    inset: 0;
    background:
      radial-gradient(ellipse 40% 55% at 22% 40%, rgba(247,143,32,0.45), transparent 70%),
      radial-gradient(ellipse 35% 50% at 78% 30%, rgba(247,143,32,0.35), transparent 70%);
  }
  .front__brand {
    position: absolute;
    left: 0; right: 0;
    top: 122px;
    display: flex;
    align-items: center;
    justify-content: center;
    gap: 14px;
    color: #ffffff;
    font-family: "Cinzel", serif;
    font-size: 34px;
    letter-spacing: 1px;
  }
  .brand__dot {
    width: 22px; height: 22px;
    border-radius: 50%;
    background: currentColor;
  }
  /* Back side */
  .card--back {
    left: 580px;
    top: 450px;
    background: var(--card-white);
  }
  .back__decor {
    position: absolute;
    right: -40px;
    top: -30px;
    width: 300px;
    height: 300px;
    border-radius: 50%;
    background: radial-gradient(circle at 45% 45%, rgba(247,143,32,0.10), rgba(140,198,63,0.10) 55%, rgba(51,166,215,0.07) 75%, transparent 78%);
  }
  .back__brand {
    position: absolute;
    left: 36px;
    top: 64px;
    display: flex;
    align-items: center;
    gap: 14px;
    font-family: "Cinzel", serif;
    font-size: 30px;
    color: var(--ink);
    letter-spacing: 0.5px;
  }
  .back__brand .brand__dot {
    width: 40px; height: 40px;
    background: var(--green-deep);
  }
  .back__address {
    position: absolute;
    right: 30px;
    top: 150px;
    text-align: right;
    font-size: 14px;
    line-height: 1.3;
    color: var(--ink-soft);
  }
  .back__person {
    position: absolute;
    left: 36px;
    top: 180px;
  }
  .person__name {
    font-size: 20px;
    font-weight: 700;
    color: var(--name-green);
    letter-spacing: 0.3px;
  }
  .person__title {
    font-size: 15px;
    color: var(--ink-soft);
    margin-top: 1px;
  }
  .contact-list {
    list-style: none;
    margin-top: 18px;
  }
  .contact-list li {
    display: flex;
    align-items: center;
    gap: 8px;
    font-size: 15px;
    color: var(--ink);
    line-height: 1.45;
  }
  .contact-list svg { width: 13px; height: 13px; fill: var(--green-deep); }
</style>
</head>
<body>
  <section class="card card--front" aria-label="Card front">
    <div class="front__glow" role="img" aria-label="Soft orange, green and blue wing-shaped glow"></div>
    <div class="front__brand">
      <span class="brand__dot"></span>
      <span class="brand__name">TARWICK &amp; CO</span>
    </div>
  </section>

  <section class="card card--back" aria-label="Card back">
    <div class="back__decor" role="img" aria-label="Faint brand decoration"></div>
    <div class="back__brand">
      <span class="brand__dot"></span>
      <span class="brand__name">TARWICK &amp; CO</span>
    </div>
    <address class="back__address" style="font-style:normal">
      87, Harbour Row<br>Calverton, 30918
    </address>
    <div class="back__person">
      <p class="person__name">DANIEL HARTLEY</p>
      <p class="person__title">Managing Director</p>
      <ul class="contact-list">
        <li>
          <svg viewBox="0 0 16 16" aria-hidden="true"><path d="M3.5 1.5l2.5 3-1.5 1.5c.8 2 2.5 3.7 4.5 4.5L10.5 9l3 2.5-1.5 2.5c-5 0-10.5-5.5-10.5-10.5z"/></svg>
          044-870 215 346
        </li>
        <li>
          <svg viewBox="0 0 16 16" aria-hidden="true"><path d="M1 3h14v10H1z M1 3l7 6 7-6" fill="none" stroke="#4fb548" stroke-width="1.6"/><path d="M1 3h14L8 8.5z"/></svg>
          hello@tarwickco.com
        </li>
      </ul>
    </div>
  </section>
</body>
</html>
```